Corvane Business Cards

Front of business card will have logo, name, address, & telephone number. Back of card will have a list of services provided - Roads, Substation Pads, Temporary Pads, Site Pads, Land Leveling, Powerline Row Cleaning, Land Clearing, Gates, Fencing, Construction Entrances, Excavation, Trenching, Underground Utilities, Directional Boring, Pile Driving. We are a construction company that uses heavy equipment like bulldozers, motor graders/blades, dump trucks, backhoes, hydro axes, & skid loaders. We build roads, pads, & install electric utility lines & waterlines underground. This logo is new. The word "Construction" can be smaller as uploaded 2 example edited logos. We will be using this card design for many employees.
Target Market(s)
Industrial Electric Powerline, Wind Turbine, Solar Panel, & Water Utility companies.
Contact Information for Business Card
Name/Position - Dwayne Halster - Owner
Address: 4875 FM 309
Harlow, TX 79412
Phone number - (325) 482-5096

```html
<!DOCTYPE html>
<html lang="en">
<head>
<meta charset="utf-8">
<title>Corvane Business Cards</title>
<link rel="stylesheet" href="https://fonts.googleapis.com/css2?family=Arimo:wght@400;700&display=swap">
<style>
  :root {
    --maroon: #3a1019;
    --white: #ffffff;
    --backdrop: #d6d6d6;
    --shadow: rgba(0,0,0,0.35);
  }
  * { margin: 0; padding: 0; box-sizing: border-box; }
  html, body {
    width: 1200px; height: 802px; overflow: hidden;
    background: var(--backdrop);
    font-family: "Arimo", Arial, sans-serif;
  }
  .stage { position: relative; width: 1200px; height: 802px; }
  .card {
    position: absolute; top: 274px;
    width: 442px; height: 265px;
    background: var(--maroon);
    box-shadow: 2px 3px 6px var(--shadow);
    overflow: hidden;
  }
  .card--front { left: 136px; }
  .card--back { left: 624px; }

  .front-wedge { position: absolute; inset: 0; width: 442px; height: 265px; }
  .front-brand {
    position: absolute; left: 26px; top: 117px;
    display: flex; align-items: center; gap: 8px;
    color: var(--maroon); font-weight: 700; font-size: 27px; letter-spacing: 1px;
  }
  .brand-dot { width: 14px; height: 14px; border-radius: 50%; background: var(--maroon); }

  .contact {
    position: absolute; right: 35px; top: 0; text-align: right; color: var(--white);
  }
  .contact-name { position: absolute; right: 0; top: 38px; white-space: nowrap; font-weight: 700; font-size: 19px; }
  .contact-role { position: absolute; right: 0; top: 62px; font-size: 13.5px; }
  .contact-address { position: absolute; right: 0; top: 163px; white-space: nowrap; font-size: 14px; line-height: 17px; }
  .contact-phone { position: absolute; right: 0; top: 212px; white-space: nowrap; font-weight: 700; font-size: 16px; }

  .back-brand {
    position: absolute; left: 22px; top: 108px; width: 190px;
    text-align: center; color: var(--white); font-weight: 700;
  }
  .back-brand-name { font-size: 33px; letter-spacing: 1px; line-height: 1; }
  .back-brand-sub { font-size: 17px; letter-spacing: 0.5px; margin-top: 8px; }

  .divider { position: absolute; left: 220px; top: 61px; width: 1px; height: 142px; background: var(--white); }
  .services {
    position: absolute; left: 239px; top: 59px; list-style: none;
    color: var(--white); font-size: 12.7px; line-height: 16.3px; white-space: nowrap;
  }
</style>
</head>
<body>
<main class="stage">
  <section class="card card--front" aria-label="Business card front">
    <svg class="front-wedge" viewBox="0 0 442 265" aria-hidden="true">
      <polygon points="0,0 80,0 305,132 80,265 0,265" fill="#ffffff"/>
    </svg>
    <div class="front-brand"><span class="brand-dot"></span><span>CORVANE</span></div>
    <div class="contact">
      <p class="contact-name">DWAYNE HALSTER</p>
      <p class="contact-role">Owner</p>
      <p class="contact-address">4875 FM 309<br>Harlow, TX 79412</p>
      <p class="contact-phone">P: (325) 482-5096</p>
    </div>
  </section>

  <section class="card card--back" aria-label="Business card back">
    <div class="back-brand">
      <p class="back-brand-name">CORVANE</p>
      <p class="back-brand-sub">CONSTRUCTION</p>
    </div>
    <div class="divider"></div>
    <ul class="services">
      <li>Roads | Substation Pads</li>
      <li>Temporary Pads | Site Pads</li>
      <li>Land Leveling | Powerline</li>
      <li>Row Cleaning | Land Clearing</li>
      <li>Gates | Fencing</li>
      <li>Construction Entrances</li>
      <li>Excavation | Trenching</li>
      <li>Underground Utilities</li>
      <li>Directional Boring | Pile Driving.</li>
    </ul>
  </section>
</main>
</body>
</html>
```